Kentucky residential recovery center needs a flyer design

We need a flyer design for a 16 bed male residential/inpatient recovery center based in Richmond, Kentucky. The facility provides short term (average 30 day) treatment to those struggling with substace abuse and addiction. The design should communicate trust, assurance, safety.
Our wesite provides more information https://corvalmend.org/treatment-services/residential-treatment/

Target Market(s)

Men (typically 30-50) struggling with substance addiction

```html
<!DOCTYPE html>
<html lang="en">
<head>
<meta charset="utf-8">
<title>Corvalmend Health – Residential/Inpatient Treatment Flyer</title>
<link rel="stylesheet" href="https://fonts.googleapis.com/css2?family=Noto+Serif:wght@400;700&family=Poppins:wght@400;500;600&display=swap">
<style>
  :root{
    --navy:#17157f;
    --navy-deep:#100e6b;
    --green:#19a83a;
    --green-dark:#12872d;
    --grey-box:#efefef;
    --white:#ffffff;
    --photo-sky:#6f9bd6;
    --photo-warm:#b8a486;
    --photo-room:#8a7155;
    --sans:'Poppins', Arial, sans-serif;
    --serif:'Noto Serif', Georgia, serif;
  }
  *{box-sizing:border-box;margin:0;padding:0}
  html,body{width:682px;height:1200px;overflow:hidden;background:var(--white)}
  .flyer{position:relative;width:682px;height:1200px;overflow:hidden;background:var(--white);font-family:var(--sans)}
  .shapes{position:absolute;inset:0}

  .brand{position:absolute;left:18px;top:26px;width:120px;text-align:center}
  .brand-mark{width:58px;height:58px;border-radius:50%;background:var(--navy);margin:0 auto 8px}
  .brand-name{font-family:var(--sans);font-weight:600;font-size:11px;letter-spacing:1.5px;color:var(--navy);line-height:1.3}

  .headline{position:absolute;left:152px;top:40px}
  .headline-sub{font-family:var(--serif);font-weight:700;font-size:23px;color:var(--navy);line-height:1.2}
  .headline-main{font-family:var(--serif);font-weight:700;font-size:40px;color:var(--green);line-height:1.15}

  .duration-box{position:absolute;left:17px;top:182px;width:335px;height:106px;background:var(--grey-box);padding:10px 16px}
  .duration-title{font-weight:600;font-size:30px;color:var(--navy);line-height:1.2}
  .duration-text{font-weight:500;font-size:15px;color:var(--green);line-height:1.35;margin-top:4px}

  .intro{position:absolute;left:17px;top:642px;width:290px;color:var(--white)}
  .intro-lead{font-weight:600;font-size:14px;letter-spacing:.3px}
  .intro-address{font-size:11px;line-height:1.5;letter-spacing:.4px}
  .intro-body{font-size:11px;line-height:1.55;margin-top:8px}

  .section-title{font-family:var(--serif);font-size:22px;line-height:1.3;text-transform:uppercase}
  .issues-title{position:absolute;left:17px;top:832px}
  .issues-title .line-a{color:var(--white)}
  .issues-title .line-b{color:var(--navy)}

  .issue{position:absolute;display:flex;align-items:center;gap:12px;color:var(--white);font-weight:500;font-size:11px;line-height:1.3;text-transform:uppercase}
  .icon-ring{width:40px;height:40px;border-radius:50%;background:var(--white);border:2px solid var(--green-dark);box-shadow:0 0 0 2px var(--white);display:flex;align-items:center;justify-content:center;flex:none}
  .icon-ring svg{width:22px;height:22px}

  .work-title{position:absolute;left:343px;top:684px}
  .work-title .line-a{color:var(--green)}
  .work-title .line-b{color:var(--white)}

  .step{position:absolute;left:343px;width:325px;display:flex;align-items:center;gap:24px;color:var(--white);font-size:11.5px;line-height:1.45}

  .badges{position:absolute;left:20px;top:1100px;display:flex;gap:26px;align-items:center}
  .badge{width:66px;height:66px;border-radius:50%}
  .badge-gold{background:radial-gradient(circle,#f2c94c 45%,#c99a1e 100%)}
  .badge-laurel{background:var(--white);border:3px dotted var(--green)}
  .badge-seal{background:#3bb4e6;border-radius:14px;transform:rotate(45deg);width:56px;height:56px;margin:0 6px}

  .contact{position:absolute;left:348px;top:1088px;color:var(--white)}
  .contact-row{display:flex;align-items:center;gap:12px}
  .contact-phone{font-weight:600;font-size:31px;letter-spacing:.5px}
  .contact-small{font-size:14px;letter-spacing:.3px;margin-top:2px}
  .contact svg{flex:none}
</style>
</head>
<body>
<main class="flyer">
  <svg class="shapes" width="682" height="1200" viewBox="0 0 682 1200" aria-hidden="false">
    <defs>
      <linearGradient id="portrait-tone" x1="0" y1="0" x2="0" y2="1">
        <stop offset="0" stop-color="var(--photo-sky)"/>
        <stop offset=".55" stop-color="#8c8f96"/>
        <stop offset="1" stop-color="#a9705e"/>
      </linearGradient>
      <linearGradient id="room-tone" x1="0" y1="0" x2="0" y2="1">
        <stop offset="0" stop-color="#c9b79a"/>
        <stop offset=".6" stop-color="var(--photo-room)"/>
        <stop offset="1" stop-color="#5f4a38"/>
      </linearGradient>
    </defs>

    <!-- left green panel -->
    <polygon points="0,388 340,330 340,1078 0,1078" fill="var(--green)"/>
    <!-- right navy panel -->
    <rect x="324" y="590" width="358" height="475" fill="var(--navy)"/>
    <polygon points="600,720 682,690 682,760" fill="var(--white)"/>

    <!-- portrait frame -->
    <path d="M352 610 L352 195 Q352 168 376 152 L586 14 Q604 3 622 14 L682 58 V610 Z" fill="url(#portrait-tone)" role="img" aria-label="Photo of a smiling resident holding his program completion certificate outside the facility"/>
    <path d="M352 240 L352 195 Q352 168 376 152 L586 14 Q604 3 622 14 L682 58" fill="none" stroke="var(--green)" stroke-width="7"/>

    <!-- facility photo circles -->
    <circle cx="142" cy="460" r="121" fill="url(#room-tone)" stroke="var(--green-dark)" stroke-width="5" role="img" aria-label="Photo of the facility living room with leather sofas, rug and television"/>
    <circle cx="377" cy="530" r="95" fill="url(#room-tone)" stroke="var(--green-dark)" stroke-width="5" role="img" aria-label="Photo of a lounge with sofa and coffee table"/>
    <circle cx="578" cy="632" r="86" fill="url(#room-tone)" stroke="var(--green-dark)" stroke-width="5" role="img" aria-label="Photo of a bedroom with bunk bed and couch"/>

    <!-- bottom contact band -->
    <path d="M352 1066 L682 1046 V1062 L352 1082 Z" fill="var(--white)"/>
    <path d="M282 1200 L338 1098 Q350 1078 378 1076 L682 1058 V1200 Z" fill="var(--green)"/>
  </svg>

  <div class="brand">
    <div class="brand-mark"></div>
    <div class="brand-name">CORVALMEND HEALTH</div>
  </div>

  <header class="headline">
    <div class="headline-sub">Residential/Inpatient</div>
    <div class="headline-main">Treatment</div>
  </header>

  <section class="duration-box">
    <div class="duration-title">30 day Treatment</div>
    <div class="duration-text">to those struggling with substace<br>abuse and addiction</div>
  </section>

  <section class="intro">
    <div class="intro-lead">16 bed male residential/inpatient</div>
    <div class="intro-address">recovery center based in 1410 &amp; 1412<br>Birchline Drive, Richmond, Kentucky 40475</div>
    <p class="intro-body">94% of those suffering from substance use disorder stay in active addiction without an intervention. We offer the most effective and comfortable treatment that leads to success.</p>
  </section>

  <h2 class="section-title issues-title"><span class="line-a">What issues</span><br><span class="line-b">can be treated?</span></h2>

  <div class="issue" style="left:17px;top:918px">
    <span class="icon-ring"><svg viewBox="0 0 24 24" fill="none" stroke="var(--green)" stroke-width="1.6"><path d="M10 2h4v5l2 3v12H8V10l2-3z"/><rect x="9.5" y="13" width="5" height="5"/></svg></span>
    Alcoholism
  </div>
  <div class="issue" style="left:168px;top:918px">
    <span class="icon-ring"><svg viewBox="0 0 24 24" fill="none" stroke="var(--green)" stroke-width="1.6"><rect x="3" y="9" width="18" height="7" rx="3.5" transform="rotate(-40 12 12)"/><path d="M10 8l5 6"/></svg></span>
    Medication<br>addiction
  </div>
  <div class="issue" style="left:17px;top:990px">
    <span class="icon-ring"><svg viewBox="0 0 24 24" fill="none" stroke="var(--green)" stroke-width="1.6"><path d="M4 20l4-4M7 13l4 4M8 12l8-8 4 4-8 8zM17 3l4 4"/></svg></span>
    Drug<br>addiction
  </div>
  <div class="issue" style="left:168px;top:990px">
    <span class="icon-ring"><svg viewBox="0 0 24 24" fill="none" stroke="var(--green)" stroke-width="1.6"><path d="M6 20v-4a7 7 0 1 1 9 3v1z"/><circle cx="12" cy="10" r="3"/></svg></span>
    Behavioral<br>health
  </div>

  <h2 class="section-title work-title"><span class="line-a">How does</span><br><span class="line-b">it work?</span></h2>

  <div class="step" style="top:785px">
    <span class="icon-ring"><svg viewBox="0 0 24 24" fill="none" stroke="var(--green)" stroke-width="1.6"><path d="M4 5h16v10H10l-4 4v-4H4z"/><path d="M8 9h8M8 12h5"/></svg></span>
    <span>Speak with our team in private about the nature of your challenges and what you need help with</span>
  </div>
  <div class="step" style="top:874px">
    <span class="icon-ring"><svg viewBox="0 0 24 24" fill="none" stroke="var(--green)" stroke-width="1.6"><circle cx="12" cy="8" r="4"/><path d="M4 21c0-5 4-7 8-7s8 2 8 7z"/></svg></span>
    <span>Together we select an appropriate time slot to book you in for an induction appointment with one of our clinical staff.</span>
  </div>
  <div class="step" style="top:960px">
    <span class="icon-ring"><svg viewBox="0 0 24 24" fill="none" stroke="var(--green)" stroke-width="1.6"><circle cx="12" cy="12" r="9"/><path d="M10 8l6 4-6 4z"/></svg></span>
    <span>Once the induction is completed, we'll schedule you in to commence your inpatient program</span>
  </div>

  <div class="badges">
    <div class="badge badge-gold"></div>
    <div class="badge badge-laurel"></div>
    <div class="badge badge-seal"></div>
  </div>

  <address class="contact" style="font-style:normal">
    <div class="contact-row contact-phone">
      <svg width="20" height="20" viewBox="0 0 24 24" fill="var(--white)"><path d="M6.6 10.8a15 15 0 0 0 6.6 6.6l2.2-2.2c.3-.3.7-.4 1-.2 1.1.4 2.3.6 3.6.6.6 0 1 .4 1 1V20c0 .6-.4 1-1 1A17 17 0 0 1 3 4c0-.6.4-1 1-1h3.5c.6 0 1 .4 1 1 0 1.3.2 2.5.6 3.6.1.3 0 .7-.2 1z"/></svg>
      859 555-0142
    </div>
    <div class="contact-row contact-small">
      <svg width="14" height="14" viewBox="0 0 24 24" fill="none" stroke="var(--white)" stroke-width="2"><rect x="3" y="5" width="18" height="14"/><path d="M3 5l9 8 9-8"/></svg>
      admissions@corvalmend.com
    </div>
    <div class="contact-row contact-small">
      <svg width="14" height="14" viewBox="0 0 24 24" fill="none" stroke="var(--white)" stroke-width="2"><circle cx="12" cy="12" r="9"/><path d="M3 12h18M12 3c3 3 3 15 0 18M12 3c-3 3-3 15 0 18"/></svg>
      www.corvalmend.org
    </div>
  </address>
</main>
</body>
</html>
```